Stationery & Envelope Design

Executive Style looking stationery & envelope design.
Business Information:
TKL Executive Realty
2875 Birchwood Lane, Roseville, CA 95661-4180
Phone: 916.555.0142
Fax: 916.555.0187

Industry/Entity Type

Business

```html
<!DOCTYPE html>
<html lang="en">
<head>
<meta charset="utf-8">
<title>TKL Executive Realty — Stationery Set</title>
<link rel="stylesheet" href="https://fonts.googleapis.com/css2?family=Arimo:wght@400;700&display=swap">
<style>
  :root {
    --navy: #1b3f86;
    --navy-deep: #1d2f66;
    --royal: #0a56a3;
    --olive: #788b33;
    --ink: #222222;
    --rule: #333333;
    --paper: #ffffff;
    --edge: #8a8a8a;
    --ground: #e9e4dc;
    --grey-mark: #5d5d5d;
  }
  * { box-sizing: border-box; margin: 0; padding: 0; }
  html, body { width: 1200px; height: 1071px; overflow: hidden; }
  body {
    position: relative;
    background: var(--ground);
    font-family: "Arimo", Arial, sans-serif;
    color: var(--ink);
  }
  .sheet, .envelope {
    position: absolute;
    background: var(--paper);
    border: 1px solid var(--edge);
    box-shadow: 2px 3px 6px rgba(0,0,0,.25);
    overflow: hidden;
  }
  .brand {
    position: absolute;
    font-weight: 700;
    color: var(--navy);
    white-space: nowrap;
    display: flex;
    align-items: center;
    gap: 7px;
    line-height: 1;
  }
  .brand-dot { width: 10px; height: 10px; border-radius: 50%; background: var(--olive); }
  .sheet .brand { top: 62px; left: 50%; transform: translateX(-50%); font-size: 15px; }
  .footer-band { position: absolute; left: 0; bottom: 0; width: 100%; height: 62px; display: block; }
  .footer-text {
    position: absolute; left: 0; width: 100%;
    text-align: center; color: #fff; font-size: 9px; font-weight: 700;
    font-variant: small-caps; letter-spacing: .2px; line-height: 1;
    white-space: nowrap;
  }
  /* fax sheet */
  .fax { left: 90px; top: 34px; width: 464px; height: 600px; }
  .fax-title { position: absolute; left: 35px; top: 118px; font-size: 28px; font-weight: 400; line-height: 1; }
  .fax-fields {
    position: absolute; left: 39px; top: 175px; width: 386px;
    display: grid; grid-template-columns: 250px 136px; row-gap: 32px;
  }
  .fax-field {
    font-size: 10.5px; line-height: 1; height: 23px;
    border-bottom: 1.5px solid var(--rule);
    padding-top: 2px;
  }
  .fax-field:nth-child(even) { padding-left: 0; }
  .fax-contact { bottom: 27px; }
  .fax-contact svg { width: 8px; height: 8px; vertical-align: -1px; margin-right: 2px; }
  .fax-address { bottom: 10px; }
  /* letterhead */
  .letterhead { left: 624px; top: 35px; width: 464px; height: 600px; }
  .letterhead .brand { top: 62px; left: 31px; transform: none; }
  .lh-name { bottom: 21px; font-size: 8.5px; }
  .lh-address { bottom: 10px; font-size: 8.5px; }
  /* envelopes */
  .flap { position: absolute; left: 0; top: 0; width: 100%; height: 72px; display: block; }
  .envelope .brand { font-size: 14px; }
  .flap-brand { top: 28px; left: 50%; transform: translateX(-50%); }
  .env-olive { left: 85px; top: 667px; width: 515px; height: 222px; }
  .env-olive .brand { color: var(--olive); }
  .env-grey { left: 56px; top: 737px; width: 519px; height: 222px; }
  .env-grey .brand { color: var(--grey-mark); }
  .env-front { left: 45px; top: 814px; width: 520px; height: 225px; }
  .env-front .brand { top: 44px; left: 14px; font-size: 12px; }
  .env-front .footer-band { height: 64px; }
  .env-name { bottom: 28px; font-size: 8.5px; }
  .env-address { bottom: 16px; font-size: 8.5px; }
  .env-green { left: 619px; top: 659px; width: 519px; height: 292px; }
  .env-green .brand { color: #fff; }
  .env-blue { left: 605px; top: 728px; width: 518px; height: 222px; }
  .env-blue .brand { color: #fff; }
  .env-blue .brand-dot, .env-green .brand-dot { background: #fff; }
  .env-black { left: 638px; top: 807px; width: 519px; height: 227px; }
  .env-black .brand { color: #111; }
  .env-black .brand-dot, .env-grey .brand-dot { background: currentColor; }
</style>
</head>
<body>

  <section class="sheet fax" aria-label="Fax cover sheet">
    <div class="brand"><span class="brand-dot"></span>TKL Executive Realty</div>
    <h1 class="fax-title">FAX</h1>
    <div class="fax-fields">
      <div class="fax-field">To</div><div class="fax-field">From</div>
      <div class="fax-field">Fax</div><div class="fax-field">Pages</div>
      <div class="fax-field">Phone</div><div class="fax-field">Date</div>
      <div class="fax-field">Re</div><div class="fax-field">CC</div>
    </div>
    <svg class="footer-band" viewBox="0 0 464 62" preserveAspectRatio="none" aria-hidden="true">
      <defs><linearGradient id="bandFax" x1="0" x2="1"><stop offset="0" stop-color="#0a56a3"/><stop offset="1" stop-color="#1d2f66"/></linearGradient></defs>
      <path d="M0 34 Q232 -14 464 34 L464 37 Q232 -9 0 37 Z" fill="#788b33"/>
      <path d="M0 42 Q232 -2 464 42 L464 62 L0 62 Z" fill="url(#bandFax)"/>
    </svg>
    <p class="footer-text fax-contact">
      <svg viewBox="0 0 10 10"><path d="M2 1 L4 1 L5 3 L4 4 Q5 6 6 6 L7 5 L9 6 L9 8 Q6 9 3 6 Q1 4 2 1Z" fill="#fff"/></svg>916.555.0142
      &nbsp;<svg viewBox="0 0 10 10"><rect x="1" y="4" width="8" height="5" fill="#fff"/><rect x="3" y="1" width="4" height="3" fill="#fff"/></svg>916.555.0187
    </p>
    <p class="footer-text fax-address">TKL Executive Realty, 2875 Birchwood Lane, Roseville, CA 95661-4180</p>
  </section>

  <section class="sheet letterhead" aria-label="Letterhead">
    <div class="brand"><span class="brand-dot"></span>TKL Executive Realty</div>
    <svg class="footer-band" viewBox="0 0 464 62" preserveAspectRatio="none" aria-hidden="true">
      <defs><linearGradient id="bandLh" x1="0" x2="1"><stop offset="0" stop-color="#0a56a3"/><stop offset="1" stop-color="#1d2f66"/></linearGradient></defs>
      <path d="M0 46 Q232 -4 464 34 L464 37 Q232 1 0 49 Z" fill="#788b33"/>
      <path d="M0 53 Q232 8 464 42 L464 62 L0 62 Z" fill="url(#bandLh)"/>
    </svg>
    <p class="footer-text lh-name">TKL Executive Realty</p>
    <p class="footer-text lh-address">2875 Birchwood Lane, Roseville, CA 95661-4180</p>
  </section>

  <section class="envelope env-olive" aria-label="Envelope back, olive mark">
    <svg class="flap" viewBox="0 0 515 72" preserveAspectRatio="none" aria-hidden="true"><path d="M0 0 L18 72 L497 72 L515 0" fill="none" stroke="#8a8a8a"/></svg>
    <div class="brand flap-brand"><span class="brand-dot"></span>TKL Executive Realty</div>
  </section>

  <section class="envelope env-grey" aria-label="Envelope back, grey mark">
    <svg class="flap" viewBox="0 0 519 72" preserveAspectRatio="none" aria-hidden="true"><path d="M0 0 L18 72 L501 72 L519 0" fill="none" stroke="#8a8a8a"/></svg>
    <div class="brand flap-brand"><span class="brand-dot"></span>TKL Executive Realty</div>
  </section>

  <section class="envelope env-front" aria-label="Envelope front">
    <div class="brand"><span class="brand-dot"></span>TKL Executive Realty</div>
    <svg class="footer-band" viewBox="0 0 520 64" preserveAspectRatio="none" aria-hidden="true">
      <defs><linearGradient id="bandEnv" x1="0" x2="1"><stop offset="0" stop-color="#0a56a3"/><stop offset="1" stop-color="#1d2f66"/></linearGradient></defs>
      <path d="M0 30 Q260 -12 520 34 L520 37 Q260 -7 0 33 Z" fill="#788b33"/>
      <path d="M0 40 Q260 0 520 44 L520 64 L0 64 Z" fill="url(#bandEnv)"/>
    </svg>
    <p class="footer-text env-name">TKL Executive Realty</p>
    <p class="footer-text env-address">2875 Birchwood Lane, Roseville, CA 95661-4180</p>
  </section>

  <section class="envelope env-green" aria-label="Envelope back, olive flap">
    <svg class="flap" viewBox="0 0 519 70" preserveAspectRatio="none" aria-hidden="true"><path d="M0 0 L519 0 L505 70 L14 70 Z" fill="#788b33"/></svg>
    <div class="brand flap-brand"><span class="brand-dot"></span>TKL Executive Realty</div>
  </section>

  <section class="envelope env-blue" aria-label="Envelope back, blue flap">
    <svg class="flap" viewBox="0 0 518 72" preserveAspectRatio="none" aria-hidden="true"><path d="M0 0 L518 0 L500 72 L18 72 Z" fill="#0a56a3"/></svg>
    <div class="brand flap-brand"><span class="brand-dot"></span>TKL Executive Realty</div>
  </section>

  <section class="envelope env-black" aria-label="Envelope back, black mark">
    <svg class="flap" viewBox="0 0 519 72" preserveAspectRatio="none" aria-hidden="true"><path d="M0 0 L14 72 L505 72 L519 0" fill="none" stroke="#8a8a8a"/></svg>
    <div class="brand flap-brand"><span class="brand-dot"></span>TKL Executive Realty</div>
  </section>

</body>
</html>
```